Simple Business Card Design for Tavlo

Job:

Make a very simple, minimalist business card design with my details including adjusted logo. One side to be white (with logo & text). Other side to be yellow - try plain or with logo (or part of logo eg Z). Need business card to have continuity with website.

Logo:
Our logo is made from a free download font website:
http://www.typewell.net/search.php?q=rubber
but the spacing/kerning needs correcting/adjusting as the font spaces unevenly between letters (see attached files). Need logo to be very crisp/sharp when printed.

Printing:
We will be using Plika.com so the design needs to conform to their requirements, see here:

http://uk.plika.com/products/luxe/business-cards.html (scroll down for dimensions and guidelines)

Design:

must say "plant-based food consulting" underneath logo or somewhere
no address needed in contact section
sharp corners (not rounded)
one side white, one side yellow

name: Rosalind Whitcombe
1xmobile number: +44 7700900463
1xtwiiter: @brimcounsel
website address www.orchardtable.com
email address brim@orchardtable.com

Should be easy quick job, prompt + detailed feedback given, am online in UK 9am-10pm for next 3 days. Website is www.orchardtable.com

Industry/Entity Type

Business

Requirements
Must have
• The logo must be corrected. The kerning is not right.

Please use a warm-grey for text

Please submit in matt format, we will be printing matt finish.

Should not have
• Avoid using banners or curvy highlights

Please avoid using black

Please avoid submitting in gloss finish

```html
<!DOCTYPE html>
<html lang="en">
<head>
<meta charset="utf-8">
<title>Brim business cards</title>
<link href="https://fonts.googleapis.com/css2?family=Mulish:wght@400;600;700&display=swap" rel="stylesheet">
<style>
  :root {
    --backdrop: #4a4a4a;
    --card-white: #f7f7f5;
    --card-yellow: #e8a800;
    --accent: #e8a800;
    --warm-grey: #6b6560;
    --warm-grey-deep: #4e4843;
    --rule-white: #e2e0dc;
    --rule-yellow: #c99200;
  }
  * { margin: 0; padding: 0; box-sizing: border-box; }
  html, body { width: 1200px; height: 1000px; overflow: hidden; }
  body {
    background: var(--backdrop);
    font-family: "Mulish", "Century Gothic", sans-serif;
    position: relative;
  }
  .card {
    position: absolute;
    width: 532px;
    height: 303px;
    color: var(--warm-grey);
  }
  .card--white  { left: 205px; top: 163px; background: var(--card-white); }
  .card--yellow { left: 473px; top: 550px; background: var(--card-yellow); color: var(--warm-grey-deep); }

  .brand {
    position: absolute;
    left: 50px;
    top: 116px;
    width: 170px;
  }
  .brand__name {
    font-size: 56px;
    line-height: 56px;
    font-weight: 600;
    letter-spacing: 4px;
    color: var(--accent);
  }
  .card--yellow .brand__name { color: var(--warm-grey-deep); }
  .brand__tagline {
    margin-top: 8px;
    font-size: 11.5px;
    line-height: 14px;
    letter-spacing: 0.3px;
    white-space: nowrap;
  }

  .divider {
    position: absolute;
    left: 251px;
    top: 58px;
    width: 1px;
    height: 190px;
    background: var(--rule-white);
  }
  .card--yellow .divider { background: var(--rule-yellow); }

  .details { position: absolute; left: 297px; top: 88px; }
  .person__name {
    font-size: 16px;
    font-weight: 700;
    letter-spacing: 0.6px;
    line-height: 20px;
    white-space: nowrap;
  }
  .person__role { font-size: 12.5px; line-height: 18px; }
  .contact { list-style: none; margin-top: 20px; }
  .contact__item {
    display: flex;
    align-items: center;
    font-size: 13px;
    line-height: 18px;
    height: 18px;
    white-space: nowrap;
  }
  .contact__icon {
    width: 12px; height: 12px; margin-right: 7px; flex: none;
    color: var(--accent);
  }
  .card--yellow .contact__icon { color: var(--warm-grey-deep); }
</style>
</head>
<body>

<svg width="0" height="0" style="position:absolute">
  <defs>
    <symbol id="icon-phone" viewBox="0 0 12 12">
      <circle cx="6" cy="6" r="5.3" fill="none" stroke="currentColor" stroke-width="1"/>
      <path d="M4 3.2 L5 3 L5.6 4.6 L5 5.1 Q5.6 6.5 6.9 7 L7.4 6.4 L9 7 L8.8 8 Q6.8 8.6 5 6.8 Q3.4 5.2 4 3.2 Z" fill="currentColor"/>
    </symbol>
    <symbol id="icon-handle" viewBox="0 0 12 12">
      <circle cx="6" cy="6" r="5.3" fill="none" stroke="currentColor" stroke-width="1"/>
      <circle cx="6" cy="6" r="2" fill="currentColor"/>
    </symbol>
    <symbol id="icon-mail" viewBox="0 0 12 12">
      <circle cx="6" cy="6" r="5.3" fill="none" stroke="currentColor" stroke-width="1"/>
      <rect x="3.2" y="4" width="5.6" height="4" fill="none" stroke="currentColor" stroke-width="0.8"/>
      <path d="M3.2 4 L6 6.2 L8.8 4" fill="none" stroke="currentColor" stroke-width="0.8"/>
    </symbol>
    <symbol id="icon-web" viewBox="0 0 12 12">
      <circle cx="6" cy="6" r="5.3" fill="none" stroke="currentColor" stroke-width="1"/>
      <ellipse cx="6" cy="6" rx="2.2" ry="5.3" fill="none" stroke="currentColor" stroke-width="0.8"/>
      <path d="M0.7 6 H11.3 M1.6 3.5 H10.4 M1.6 8.5 H10.4" stroke="currentColor" stroke-width="0.8"/>
    </symbol>
  </defs>
</svg>

<section class="card card--white">
  <div class="brand">
    <p class="brand__name">BRIM</p>
    <p class="brand__tagline">plant-based food consulting</p>
  </div>
  <div class="divider"></div>
  <div class="details">
    <p class="person__name">ROSALIND WHITCOMBE</p>
    <p class="person__role">General Manager</p>
    <ul class="contact">
      <li class="contact__item"><svg class="contact__icon"><use href="#icon-phone"/></svg>+44 7700900463</li>
      <li class="contact__item"><svg class="contact__icon"><use href="#icon-handle"/></svg>@brimcounsel</li>
      <li class="contact__item"><svg class="contact__icon"><use href="#icon-mail"/></svg>brim@orchardtable.com</li>
      <li class="contact__item"><svg class="contact__icon"><use href="#icon-web"/></svg>www.orchardtable.com</li>
    </ul>
  </div>
</section>

<section class="card card--yellow">
  <div class="brand">
    <p class="brand__name">BRIM</p>
    <p class="brand__tagline">plant-based food consulting</p>
  </div>
  <div class="divider"></div>
  <div class="details">
    <p class="person__name">ROSALIND WHITCOMBE</p>
    <p class="person__role">General Manager</p>
    <ul class="contact">
      <li class="contact__item"><svg class="contact__icon"><use href="#icon-phone"/></svg>+44 7700900463</li>
      <li class="contact__item"><svg class="contact__icon"><use href="#icon-handle"/></svg>@brimcounsel</li>
      <li class="contact__item"><svg class="contact__icon"><use href="#icon-mail"/></svg>brim@orchardtable.com</li>
      <li class="contact__item"><svg class="contact__icon"><use href="#icon-web"/></svg>www.orchardtable.com</li>
    </ul>
  </div>
</section>

</body>
</html>
```